Satchel & Sundial needs new business card design

I need a new business card design. I'm looking for out-of-the-box design which represents the freedom of being a location independent entrepreneur.
I offer coaching, retreats and trips.
I would like to see designs with and without the photo.
Colors I use are black (#000000), green (#25A796) and brown (#D7C38C)
Website satchelandsundial.example

Target Market(s)

location independent entrepreneurs, digital nomads, people looking to swap the 9 to 5 for a lifestyle business

Industry/Entity Type

Business

Contact Information for Business Card

Dorota Falkner
Your Lifestyle Business Coach, Retreat & Trip Leader
http://satchelandsundial.example
hello@satchelandsundial.example
Live a life you don't need a holiday from

Font styles to use
Serif
Sans Serif

Requirements
Must have
• One side should contain only the logo. I would also consider having the "Live a life you don't need a holiday from" on that side too (depending on how it looks)
• Please show both sides on the designs.

```html
<!DOCTYPE html>
<html lang="en">
<head>
<meta charset="utf-8">
<title>Satchel &amp; Sundial — Business Card</title>
<link rel="stylesheet" href="https://fonts.googleapis.com/css2?family=Oswald:wght@300;400;500&display=swap">
<style>
  :root {
    --ink: #111111;
    --black: #1a1a1a;
    --green: #13897c;
    --gold: #d1be86;
    --gold-dark: #c7b47b;
    --paper: #fbfbfb;
    --rule: #d9c3ad;
    --backdrop: #e4e4e4;
    --white: #ffffff;
  }
  * { margin: 0; padding: 0; box-sizing: border-box; }
  html, body {
    width: 1200px; height: 576px; overflow: hidden;
    background: var(--backdrop);
    font-family: "Oswald", "Arial Narrow", sans-serif;
  }
  .canvas { position: relative; width: 1200px; height: 576px; }

  .card {
    position: absolute; top: 138px;
    border-radius: 7px; overflow: hidden;
  }

  /* Logo side */
  .card--front {
    left: 82px; width: 484px; height: 294px;
    background: linear-gradient(180deg, var(--gold) 0%, var(--gold-dark) 100%);
    display: flex; align-items: center; justify-content: center;
  }
  .brand-name {
    color: var(--ink); font-weight: 400; text-transform: uppercase;
    letter-spacing: 1px; line-height: 1;
  }
  .card--front .brand-name { font-size: 44px; }

  /* Contact side */
  .card--back {
    left: 602px; width: 481px; height: 291px;
    background: var(--paper);
  }
  .card--back .brand-name {
    position: absolute; left: 22px; top: 58px; font-size: 32px;
  }
  .holder {
    position: absolute; right: 22px; top: 158px; text-align: right;
  }
  .holder__name {
    font-size: 21px; font-weight: 500; color: var(--ink);
    text-transform: uppercase; line-height: 1.1;
  }
  .holder__role {
    font-size: 12.5px; font-weight: 400; color: var(--green); margin-top: 2px;
  }
  .divider {
    position: absolute; left: 22px; top: 188px;
    width: 192px; height: 1px; background: var(--rule);
  }
  .contact {
    position: absolute; left: 22px; top: 211px; list-style: none;
  }
  .contact li {
    display: flex; align-items: center; height: 20px;
    font-size: 12.5px; font-weight: 300; color: var(--ink);
  }
  .contact svg { width: 11px; height: 11px; margin-right: 12px; fill: var(--green); }
  .contact .accent { color: var(--green); }
  .social {
    position: absolute; right: 22px; top: 220px;
    font-size: 12.5px; color: var(--green); font-weight: 400;
  }
  .footer-band { position: absolute; left: 0; bottom: 0; width: 481px; height: 36px; }
  .tagline {
    position: absolute; right: 22px; bottom: 9px;
    color: var(--white); font-size: 14px; font-weight: 300;
  }
</style>
</head>
<body>
<main class="canvas">

  <section class="card card--front" aria-label="Logo side">
    <span class="brand-name">Satchel &amp; Sundial</span>
  </section>

  <section class="card card--back" aria-label="Contact side">
    <span class="brand-name">Satchel &amp; Sundial</span>

    <div class="holder">
      <p class="holder__name">Dorota Falkner</p>
      <p class="holder__role">Your Lifestyle Business Coach, Retreat &amp; Trip Leader</p>
    </div>

    <div class="divider"></div>

    <ul class="contact">
      <li>
        <svg viewBox="0 0 12 12" aria-hidden="true"><path d="M0 2h12v8H0z M0 2l6 4.5L12 2" /><path d="M0.8 2.6L6 6.4l5.2-3.8v0.9L6 7.3 0.8 3.5z" fill="#fbfbfb"/></svg>
        hello@satchelandsundial.example
      </li>
      <li>
        <svg viewBox="0 0 12 12" aria-hidden="true"><circle cx="6" cy="6" r="5.5"/><path d="M0.5 6h11M6 0.5v11M6 0.5c-3 3-3 8 0 11M6 0.5c3 3 3 8 0 11" stroke="#fbfbfb" stroke-width="0.8" fill="none"/></svg>
        www.<span class="accent">satchelandsundial</span>.example
      </li>
    </ul>

    <p class="social">/satchelandsundial</p>

    <svg class="footer-band" viewBox="0 0 481 36" aria-hidden="true">
      <polygon points="0,19 224,19 213,36 0,36" fill="var(--green)"/>
      <polygon points="233,0 481,0 481,36 213,36" fill="var(--black)"/>
    </svg>
    <p class="tagline">Live a life you don't need a holiday from</p>
  </section>

</main>
</body>
</html>
```